Website Design for a Chemical Sales Company

We are working with a Chemical Sales Company in California. They sell various chemicals throughout the US.
Types of products they sell: https://www.wardenvale.example/us/products/all
https://www.molvista.example/products/kerrin/glacyn-glycol-thermal-fluids/glacyn-propylene-glycol-thermal-fluids
Some sites to use for inspiration:
https://www.molvista.example
https://www.kerrin.example/en-us
Thank you for taking the time to consider designing a website for us. We are web developers based in Stockton, CA, USA. Most of our projects go through the same process. Understanding this process may help you win a project with us. We custom-code all of our websites in-house. We don’t have any requirements as to what tools you use for your design, but we ask that you follow these guidelines.
IMAGES:
If you use any images or icons in the design, we ask that you have a link to the asset so we can purchase the image/icon. Most of the designs we submit do not have the customer’s images on them unless they have some great images. Be creative; show us the feeling you are trying to portray with your image choices. Use any royalty-free site you choose. We subscribe to Pelmora and mainly use their images, but we can purchase images outside of Pelmora. PLEASE NOTE: we will not submit designs to clients with watermarks on the images.
FONTS:
We ask that you identify the fonts you’re using in the design. This can be done in a message if you want. We typically use Google Fonts and Pelmora Fonts.
CONTENT:
We're always open to different content and ideas. We often submit designs with stock images so the client can see our vision. We typically take pictures after the website launch to use their images with our vision. Lorem Ipsum is fine for paragraphs, but we ask that you make the Headers with correct English. We want to be able to show the vision and identify the sections of the website.
INSPIRATION:
We typically add a couple of links in the brief of websites we like to help you get started in your design.
REVISIONS:
We do not often ask for revisions of the designs unless we see something in the design that may not appeal to the client. If there are slight changes that we want to make, we do that in the development process.
FEEDBACK:
We rarely give feedback on designs during the design process. We are working on many website projects and do not have the time to provide feedback. We usually respond if your request is well thought out and asks specific questions, but a note asking “feedback, please” usually goes unanswered.

```html
<!DOCTYPE html>
<html lang="en">
<head>
<meta charset="utf-8">
<title>Ionvale – Chemical Sales</title>
<link href="https://fonts.googleapis.com/css2?family=Poppins:wght@400;500;600;700&display=swap" rel="stylesheet">
<style>
:root{
  --blue:#0e9ad8;
  --blue-dark:#0a7fbd;
  --ink:#222;
  --text:#444;
  --line:#c9c9c9;
  --pale:#e7f1f7;
  --footer:#1c2023;
  --white:#fff;
}
*{box-sizing:border-box;margin:0;padding:0}
html,body{width:1200px;height:4354px;overflow:hidden}
body{font-family:"Poppins",sans-serif;color:var(--text);background:var(--white);position:relative}
.abs{position:absolute}

/* header + hero */
.hero{left:0;top:0;width:1200px;height:620px;overflow:hidden}
.hero-photo{position:absolute;inset:0;background:linear-gradient(180deg,#a9b79a 0%,#c9b778 14%,#8a9a4d 26%,#4f7a2a 45%,#3f6e22 70%,#5e8a33 100%)}
.hero-curve{position:absolute;left:0;top:0}
.brand{left:105px;top:40px;display:flex;align-items:center;gap:10px;color:var(--white);font-size:22px;font-weight:500;letter-spacing:1px}
.brand .dot{width:14px;height:14px;border-radius:50%;background:var(--white)}
.nav{top:42px;left:583px;display:flex;gap:0;color:var(--white);font-size:17px}
.nav a{color:inherit;text-decoration:none;position:absolute;white-space:nowrap}
.lang{left:890px;top:44px;display:flex;align-items:center;gap:8px;color:var(--white);font-size:15px}
.flag{width:26px;height:18px;border-radius:3px;background:repeating-linear-gradient(180deg,#c8283a 0 3px,#fff 3px 6px);position:relative;overflow:hidden}
.flag::before{content:"";position:absolute;left:0;top:0;width:12px;height:9px;background:#2c3f8c}
.btn-login{left:997px;top:37px;width:98px;height:41px;border-radius:21px;background:var(--blue);color:var(--white);font-size:14px;font-weight:600;display:flex;align-items:center;justify-content:center}
.hero-title{left:0;width:1200px;top:162px;text-align:center;color:var(--white);font-size:37px;font-weight:700;letter-spacing:.5px;text-shadow:0 2px 6px rgba(0,0,0,.35)}
.search{left:355px;top:232px;width:490px;height:40px;border-radius:20px;background:var(--white);display:flex;align-items:center;justify-content:space-between;padding-left:20px;font-size:15px;color:#333}
.search .go{width:92px;height:36px;margin-right:2px;border-radius:18px;background:var(--blue);color:var(--white);font-weight:600;display:flex;align-items:center;justify-content:center;font-size:15px}
.mouse{left:582px;top:540px}

/* features */
.feature{width:282px;height:282px;border-radius:50%;background:var(--white);box-shadow:0 4px 14px rgba(0,0,0,.14);text-align:center;padding-top:34px}
.feature svg{display:block;margin:0 auto}
.feature h3{font-size:18px;font-weight:500;color:var(--ink);margin-top:12px}
.feature h3.accent{color:var(--blue)}
.feature p{font-size:13px;line-height:21px;margin:6px auto 0;width:232px;color:#444}
.feature .more{display:inline-block;margin-top:5px;font-size:14px;color:var(--blue);font-weight:500;border-bottom:1px solid var(--blue)}

/* products */
.products-bg{left:0;top:1014px;width:1200px;height:1068px;background:linear-gradient(160deg,#d9e9f3 0%,#eef4f8 45%,#e1ecf3 100%)}
.section-title{width:1200px;left:0;text-align:center;color:var(--blue);font-size:30px;font-weight:600}
.card{width:234px;height:338px;background:var(--white);box-shadow:0 2px 6px rgba(0,0,0,.12);text-align:center}
.card.active{border:2px solid #555}
.card .shot{margin:5px;height:178px;background:linear-gradient(180deg,#f2f2f2,#e6e6e6);position:relative}
.card .shot i{position:absolute;left:50%;top:50%;transform:translate(-50%,-50%);width:70px;height:120px;border-radius:10px}
.card .badge{position:absolute;right:12px;top:12px;width:26px;height:26px;border-radius:50%;border:2px solid #e8443a}
.card h4{font-size:18px;font-weight:600;color:var(--ink);margin-top:22px}
.card.active h4{color:var(--blue)}
.card p{font-size:12px;line-height:18px;width:200px;margin:6px auto 0}
.card .details{margin:14px auto 0;width:172px;height:37px;border:1px solid var(--blue);border-radius:19px;display:flex;align-items:center;justify-content:space-between;padding-left:18px;font-size:14px;color:var(--blue)}
.card .details span.arrow{width:35px;height:35px;border-radius:50%;background:var(--blue);display:flex;align-items:center;justify-content:center}

/* about */
.about-bg{left:0;top:2082px;width:1200px;height:588px;background:linear-gradient(90deg,#f6fafd 0%,#ffffff 40%,#eef6fb 100%)}
.about-title{left:103px;top:2188px;color:var(--blue);font-size:30px;font-weight:600}
.about-text{left:103px;top:2240px;width:462px;font-size:14.5px;line-height:25px;color:#444}
.about-text p+p{margin-top:12px}
.btn{background:var(--blue);color:var(--white);font-weight:600;font-size:14px;display:flex;align-items:center;justify-content:center;border-radius:22px}
.about-photo{left:653px;top:2162px;width:422px;height:422px;border-radius:50%;border:5px solid var(--blue);padding:14px;background:var(--white)}
.about-photo div{width:100%;height:100%;border-radius:50%;background:linear-gradient(180deg,#7b8da3 0%,#4b6a92 40%,#2c4e84 70%,#5c6f88 100%)}

/* partners */
.partners{left:0;top:2670px;width:1200px;height:195px;background:var(--blue)}
.partner{top:2731px;width:186px;height:73px;background:var(--white);display:flex;align-items:center;justify-content:center;gap:8px;font-size:16px;color:#333;font-weight:500}
.partner i{width:22px;height:22px;border-radius:50%}

/* testimonials */
.testi-bg{left:0;top:2865px;width:1200px;height:591px;background:linear-gradient(180deg,#eef2f5,#f7f8f9)}
.testi-card{left:105px;top:3022px;width:992px;height:314px;background:var(--white);border-radius:8px;box-shadow:0 3px 14px rgba(0,0,0,.12)}
.avatar{left:177px;top:3067px;width:152px;height:152px;border-radius:50%;background:linear-gradient(180deg,#d7dde2,#8b97a6)}
.person{left:105px;width:296px;text-align:center}
.divider{left:392px;top:3060px;height:233px;border-left:2px dashed #555}
.quote-text{left:446px;top:3060px;width:605px;font-size:14.5px;line-height:26.5px;color:#444}
.q{font-family:Georgia,serif;color:var(--blue);font-size:34px}

/* contact */
.skyline{left:0;top:3760px;width:1200px;height:223px;background:linear-gradient(180deg,#dfe0e2 0%,#c6c7ca 100%)}
.field{width:468px;height:54px;border:1px solid #555;border-radius:27px;background:var(--white);padding:0 15px;display:flex;align-items:center;font-size:14.5px;color:#333}
.message{left:605px;top:3613px;width:470px;height:190px;border:1px solid #555;border-radius:16px;background:var(--white);padding:14px 15px;font-size:14.5px;color:#333}

/* footer */
.footer{left:0;top:3983px;width:1200px;height:371px;background:var(--footer)}
.foot-brand{left:105px;top:4098px;display:flex;align-items:center;gap:12px;color:var(--white);font-size:34px;letter-spacing:2px}
.foot-brand i{width:40px;height:40px;border-radius:50%;border:3px solid var(--blue)}
.social{top:4188px;width:30px;height:30px;border-radius:50%}
.col-title{top:4047px;color:var(--white);font-size:22px}
.col-links{top:4089px;list-style:none;font-size:14px;line-height:29px;color:var(--white)}
.news-input{left:772px;top:4091px;width:330px;height:42px;border:1px solid #ccc;border-radius:21px;color:var(--white);font-size:14px;display:flex;align-items:center;padding-left:18px}
.foot-rule{left:0;top:4293px;width:1200px;border-top:1px solid #3a3f43}
.copy{left:0;width:1200px;top:4308px;text-align:center;color:var(--white);font-size:13px}
</style>
</head>
<body>

<!-- HERO -->
<section class="abs hero">
  <div class="hero-photo" role="img" aria-label="Tractor spraying crops in a green field at sunrise"></div>
  <svg class="hero-curve" width="1200" height="620" viewBox="0 0 1200 620">
    <path d="M0 505 Q600 650 1200 505 L1200 620 L0 620Z" fill="#0e9ad8"/>
    <path d="M0 510 Q600 640 1200 520 L1200 620 L0 620Z" fill="#fff"/>
  </svg>
</section>

<div class="abs brand"><span class="dot"></span>IONVALE</div>
<nav class="abs nav" style="left:0;width:1200px">
  <a style="left:583px">Products</a>
  <a style="left:693px">Learn</a>
  <a style="left:774px">Company</a>
</nav>
<div class="abs lang"><span class="flag"></span><span>⌄ Eng</span></div>
<div class="abs btn-login">LOG IN</div>
<h1 class="abs hero-title">WELCOME TO IONVALE</h1>
<div class="abs search">Search All Products<span class="go">GO</span></div>
<svg class="abs mouse" width="22" height="34" viewBox="0 0 22 34"><rect x="1.5" y="1.5" width="19" height="31" rx="9.5" fill="none" stroke="#0e9ad8" stroke-width="2"/><line x1="11" y1="7" x2="11" y2="13" stroke="#0e9ad8" stroke-width="2"/></svg>

<!-- FEATURES -->
<div class="abs feature" style="left:124px;top:704px">
  <svg width="72" height="76" viewBox="0 0 72 76" fill="none" stroke="#0e9ad8" stroke-width="2.5"><rect x="6" y="4" width="44" height="58"/><path d="M54 12v58H14M62 20v54H24"/><line x1="14" y1="16" x2="42" y2="16"/><rect x="14" y="24" width="12" height="10"/><line x1="30" y1="26" x2="42" y2="26"/><line x1="30" y1="32" x2="42" y2="32"/><line x1="14" y1="42" x2="42" y2="42"/><line x1="14" y1="50" x2="42" y2="50"/></svg>
  <h3>Product Articles</h3>
  <p>Lorem ipsum dolor sit amet, con-sectetur adipiscing elit, sed idunt ut labore et aliqua.</p>
  <span class="more">Read More</span>
</div>
<div class="abs feature" style="left:459px;top:704px">
  <svg width="92" height="76" viewBox="0 0 92 76" fill="none" stroke="#0e9ad8" stroke-width="2.5" stroke-linejoin="round"><path d="M4 24l16-16 14 10h14l10-6 16 6 14 16"/><path d="M20 40l18 18a6 6 0 008-8M36 52l8 8a6 6 0 008-8M46 46l10 10a6 6 0 008-8L42 26 32 34a6 6 0 01-8-8l12-10"/><path d="M74 38L60 52"/></svg>
  <h3 class="accent">Producer Partner</h3>
  <p>Lorem ipsum dolor sit amet, con-sectetur adipiscing elit, sed idunt ut labore et aliqua.</p>
  <span class="more">Read More</span>
</div>
<div class="abs feature" style="left:792px;top:704px">
  <svg width="78" height="76" viewBox="0 0 78 76" fill="none" stroke="#0e9ad8" stroke-width="2.5"><rect x="4" y="4" width="70" height="66" rx="2"/><line x1="4" y1="14" x2="74" y2="14"/><circle cx="36" cy="40" r="14"/><circle cx="36" cy="40" r="7"/><line x1="46" y1="50" x2="60" y2="64"/><line x1="12" y1="24" x2="20" y2="24"/><line x1="56" y1="26" x2="66" y2="26"/><line x1="56" y1="34" x2="66" y2="34"/></svg>
  <h3>Find the Right Product</h3>
  <p>Lorem ipsum dolor sit amet, con-sectetur adipiscing elit, sed idunt ut labore et aliqua.</p>
  <span class="more">Read More</span>
</div>

<!-- PRODUCTS -->
<div class="abs products-bg" role="img" aria-label="Soft blue laboratory background with molecular patterns"></div>
<svg class="abs" style="left:0;top:1014px" width="1200" height="90" viewBox="0 0 1200 90"><path d="M0 0 H1200 Q600 150 0 0Z" fill="#fff"/></svg>
<h2 class="abs section-title" style="top:1166px">Types Of Products</h2>

<div class="abs card" style="left:93px;top:1254px">
  <div class="shot" role="img" aria-label="Magnetic filter unit"><i style="background:#2b2b2b;width:50px;height:90px"></i></div>
  <h4>Cyclone Trap™</h4>
  <p>Lorem ipsum dolor sit amet, con-sectetur adipiscing elit aliqua.</p>
  <div class="details">Product Details<span class="arrow"><svg width="14" height="14" viewBox="0 0 14 14"><path d="M2 7h9M7 3l4 4-4 4" stroke="#fff" stroke-width="2" fill="none"/></svg></span></div>
</div>
<div class="abs card" style="left:348px;top:1254px">
  <div class="shot" role="img" aria-label="Red flushing pump machine"><i style="background:#e2402e"></i><span class="badge"></span></div>
  <h4>PulseRinse C90</h4>
  <p>Lorem ipsum dolor sit amet, con-sectetur adipiscing elit aliqua.</p>
  <div class="details">Product Details<span class="arrow"><svg width="14" height="14" viewBox="0 0 14 14"><path d="M2 7h9M7 3l4 4-4 4" stroke="#fff" stroke-width="2" fill="none"/></svg></span></div>
</div>
<div class="abs card" style="left:603px;top:1254px">
  <div class="shot" role="img" aria-label="Blue and green test kit case"><i style="background:#2a6cb8;width:120px;height:80px"></i><span class="badge"></span></div>
  <h4>PulseRinse Test Kit</h4>
  <p>Lorem ipsum dolor sit amet, con-sectetur adipiscing elit aliqua.</p>
  <div class="details">Product Details<span class="arrow"><svg width="14" height="14" viewBox="0 0 14 14"><path d="M2 7h9M7 3l4 4-4 4" stroke="#fff" stroke-width="2" fill="none"/></svg></span></div>
</div>
<div class="abs card" style="left:859px;top:1254px">
  <div class="shot" role="img" aria-label="White cleaner canister with red label"><i style="background:linear-gradient(180deg,#fff 40%,#d63a3a 40% 70%,#fff 70%);width:90px;border:1px solid #ddd"></i></div>
  <h4>S200 Solar Cleaner</h4>
  <p>Lorem ipsum dolor sit amet, con-sectetur adipiscing elit aliqua.</p>
  <div class="details">Product Details<span class="arrow"><svg width="14" height="14" viewBox="0 0 14 14"><path d="M2 7h9M7 3l4 4-4 4" stroke="#fff" stroke-width="2" fill="none"/></svg></span></div>
</div>

<div class="abs card" style="left:93px;top:1609px">
  <div class="shot" role="img" aria-label="Two white cleaner containers"><i style="background:linear-gradient(180deg,#fafafa,#e0e6ef);width:150px;height:110px;border:1px solid #ddd"></i></div>
  <h4>S200 Solar Cleaner3</h4>
  <p>Lorem ipsum dolor sit amet, con-sectetur adipiscing elit aliqua.</p>
  <div class="details">Product Details<span class="arrow"><svg width="14" height="14" viewBox="0 0 14 14"><path d="M2 7h9M7 3l4 4-4 4" stroke="#fff" stroke-width="2" fill="none"/></svg></span></div>
</div>
<div class="abs card" style="left:348px;top:1609px">
  <div class="shot" role="img" aria-label="Teal cleaner canister"><i style="background:linear-gradient(180deg,#5fd1c9,#37b8ae);width:95px"></i><span class="badge"></span></div>
  <h4>Wardenvale K400 Cleaner</h4>
  <p>Lorem ipsum dolor sit amet, con-sectetur adipiscing elit aliqua.</p>
  <div class="details">Product Details<span class="arrow"><svg width="14" height="14" viewBox="0 0 14 14"><path d="M2 7h9M7 3l4 4-4 4" stroke="#fff" stroke-width="2" fill="none"/></svg></span></div>
</div>
<div class="abs card active" style="left:603px;top:1609px">
  <div class="shot" role="img" aria-label="Yellow inhibitor canister"><i style="background:linear-gradient(180deg,#f5d43a,#e8bd14);width:95px"></i><span class="badge"></span></div>
  <h4>K100 Inhibitorprotect</h4>
  <p>Lorem ipsum dolor sit amet, con-sectetur adipiscing elit aliqua.</p>
  <div class="details">Product Details<span class="arrow"><svg width="14" height="14" viewBox="0 0 14 14"><path d="M2 7h9M7 3l4 4-4 4" stroke="#fff" stroke-width="2" fill="none"/></svg></span></div>
</div>
<div class="abs card" style="left:859px;top:1609px">
  <div class="shot" role="img" aria-label="Yellow inhibitor bottle with red nozzle"><i style="background:linear-gradient(180deg,#e23b2f 0 25%,#f6e27a 25%);width:36px;height:130px;border-radius:6px"></i></div>
  <h4>K100 Inhibitor Rapid</h4>
  <p>Lorem ipsum dolor sit amet, con-sectetur adipiscing elit aliqua.</p>
  <div class="details">Product Details<span class="arrow"><svg width="14" height="14" viewBox="0 0 14 14"><path d="M2 7h9M7 3l4 4-4 4" stroke="#fff" stroke-width="2" fill="none"/></svg></span></div>
</div>

<!-- ABOUT -->
<div class="abs about-bg" role="img" aria-label="Faint hexagon molecular background"></div>
<h2 class="abs about-title">About Us</h2>
<div class="abs about-text">
  <p>Lorem ipsum dolor sit amet, consectetur adipiscing elit, sed do eiusmod tempor incididunt ut labore et dolore magna aliqua. Ut enim ad minim veniam, quis nostrud exercitation ullamco laboris nisi ut aliquip ex ea commodo consequat. Duis aute irure dolor in reprehenderit in voluptate velit esse cillum dolore eu fugiat nulla pariatur.</p>
  <p>Sed ut perspiciatis unde omnis iste natus error sit voluptatem accusantium doloremque laudantium, totam rem aperiam, eaque ipsa quae ab illo inventore veritatis et quasi architecto beatae vitae dicta sunt explicabo.</p>
</div>
<div class="abs btn" style="left:103px;top:2508px;width:130px;height:42px">READ MORE</div>
<div class="abs about-photo"><div role="img" aria-label="Warehouse shelving stocked with chemical drums and containers"></div></div>

<!-- PARTNERS -->
<div class="abs partners"></div>
<div class="abs partner" style="left:105px"><i style="background:#0e9ad8"></i>Business Name</div>
<div class="abs partner" style="left:306px;color:#b69ad8"><i style="background:#b69ad8"></i>Chemical</div>
<div class="abs partner" style="left:507px"><i style="background:#f07a1e"></i>Science</div>
<div class="abs partner" style="left:708px;color:#1e6db5"><i style="background:#2ea34a"></i>Agrolume</div>
<div class="abs partner" style="left:909px"><i style="background:#27a8b8"></i>Science</div>

<!-- TESTIMONIALS -->
<div class="abs testi-bg" role="img" aria-label="Faded laboratory background"></div>
<h2 class="abs section-title" style="top:2940px">What Our People Says</h2>
<div class="abs testi-card"></div>
<div class="abs avatar" role="img" aria-label="Portrait of a customer holding a tablet"></div>
<div class="abs person" style="top:3233px;color:var(--blue);font-size:18px;font-weight:500">Marco Ellis</div>
<div class="abs person" style="top:3264px;font-size:14px;color:#444">Customer</div>
<div class="abs divider"></div>
<span class="abs q" style="left:413px;top:3050px">“</span>
<p class="abs quote-text">Lorem ipsum dolor sit amet, consectetur adipiscing elit, sed do eiusmod tempor in-cididunt ut labore et dolore magna aliqua. Quis ipsum suspendisse ultrices gravida. Risus commodo viverra maecenas accumsan lacus vel facilisis. Nemo enim ipsam voluptatem quia voluptas sit aspernatur aut odit aut fugit, sed quia consequuntur magni dolores eos qui ratione voluptatem sequi nesciunt. Neque porro quisquam est, qui dolorem ipsum quia dolor sit amet, consectetur, adipisci velit, sed quia non numquam eius modi tempora incidunt ut labore et dolore magnam aliquam quaerat voluptatem.</p>
<span class="abs q" style="left:616px;top:3268px">”</span>

<!-- CONTACT -->
<div class="abs skyline" role="img" aria-label="Grey city skyline silhouette"></div>
<div class="abs" style="left:0;top:3456px;width:1200px;height:300px;background:linear-gradient(180deg,#fff 80%,rgba(255,255,255,0))"></div>
<h2 class="abs section-title" style="top:3536px">Contact Us</h2>
<div class="abs field" style="left:125px;top:3613px">Name*</div>
<div class="abs field" style="left:125px;top:3681px">Email*</div>
<div class="abs field" style="left:125px;top:3749px">Phone</div>
<div class="abs message">Message</div>
<div class="abs btn" style="left:534px;top:3836px;width:130px;height:40px">SUBMIT</div>

<!-- FOOTER -->
<footer class="abs footer"></footer>
<div class="abs foot-brand"><i></i>IONVALE</div>
<span class="abs social" style="left:105px;background:var(--blue)"></span>
<span class="abs social" style="left:146px;border:1.5px solid #fff"></span>
<span class="abs social" style="left:186px;border:1.5px solid #fff"></span>

<h3 class="abs col-title" style="left:439px">Quick Links</h3>
<ul class="abs col-links" style="left:443px"><li>Home</li><li>About Us</li><li>Services</li><li>Products</li><li>Testimonials</li><li>Contact Us</li></ul>
<h3 class="abs col-title" style="left:610px">Help Links</h3>
<ul class="abs col-links" style="left:614px"><li>Products</li><li>Learn</li><li>Company</li></ul>
<h3 class="abs col-title" style="left:772px">Newsletter</h3>
<div class="abs news-input">Enter Your Name</div>
<div class="abs btn" style="left:772px;top:4149px;width:129px;height:39px">SUBMIT</div>
<div class="abs foot-rule"></div>
<p class="abs copy">Copyright © 2023 Ionvale | All Rights Reserved</p>

</body>
</html>
```